BildeVOLD buisnesscard

Hey :) I need a modern buisnesscard for my company BildeVOLD
It most have:
Dagligleder og Fotograf: Henrik Audun Strandvik

Mob: +4791264085
Epost: post@bildevold.example
Adresse: Kvernbakken9, 6040 Fjellvika

Facbook and instagram logo with text BildeVOLD

BildeVOLD logo

It Company

```html
<!DOCTYPE html>
<html lang="no">
<head>
<meta charset="utf-8">
<title>BildeVOLD – visittkort</title>
<link rel="stylesheet" href="https://fonts.googleapis.com/css2?family=Jost:wght@400;500;600;700&display=swap">
<style>
  :root {
    --page-bg: #d6d9dc;
    --card-frost: #e6e8ea;
    --navy: #1d4a7c;
    --navy-deep: #163c66;
    --berry: #ad2f5b;
    --hairline: #e9e2d4;
    --contact-text: #c8d5e4;
    --address-text: #c4b491;
    --social-dark: #1a3c6a;
    --social-gold: #b8863a;
  }
  * { margin: 0; padding: 0; box-sizing: border-box; }
  html, body {
    width: 1200px;
    height: 969px;
    overflow: hidden;
    background: var(--page-bg);
    font-family: "Jost", sans-serif;
  }
  .business-card {
    position: absolute;
    left: 360px;
    top: 64px;
    width: 480px;
    height: 840px;
    background: var(--card-frost);
    overflow: hidden;
    box-shadow: 0 10px 30px rgba(0, 0, 0, 0.18);
  }
  .card-graphics {
    position: absolute;
    inset: 0;
    width: 100%;
    height: 100%;
  }
  .brand-name {
    position: absolute;
    top: 76px;
    width: 100%;
    text-align: center;
    font-size: 76px;
    line-height: 92px;
    font-weight: 600;
    letter-spacing: -0.5px;
    color: var(--navy);
  }
  .holder-name {
    position: absolute;
    top: 184px;
    width: 100%;
    text-align: center;
    font-size: 27px;
    line-height: 36px;
    font-weight: 500;
    letter-spacing: 0.5px;
    text-transform: uppercase;
    color: var(--navy);
  }
  .holder-role {
    position: absolute;
    top: 218px;
    width: 100%;
    text-align: center;
    font-size: 25px;
    line-height: 32px;
    font-weight: 500;
    color: var(--berry);
  }
  .social-dots {
    position: absolute;
    top: 275px;
    width: 100%;
    display: flex;
    justify-content: center;
    gap: 3px;
  }
  .social-dot {
    width: 42px;
    height: 42px;
    border-radius: 50%;
  }
  .social-dot--facebook { background: var(--social-dark); }
  .social-dot--instagram { background: var(--social-gold); }
  .contact-list {
    position: absolute;
    top: 632px;
    width: 100%;
    text-align: center;
    list-style: none;
    font-size: 22px;
    line-height: 32px;
    color: var(--contact-text);
  }
  .postal-address {
    position: absolute;
    top: 744px;
    width: 100%;
    text-align: center;
    font-style: normal;
    font-size: 22px;
    line-height: 30px;
    color: var(--address-text);
  }
</style>
</head>
<body>
  <article class="business-card">
    <svg class="card-graphics" viewBox="0 0 274 480" preserveAspectRatio="none" aria-hidden="true">
      <defs>
        <linearGradient id="navyFade" x1="0" y1="0" x2="0" y2="1">
          <stop offset="0" stop-color="var(--navy)"/>
          <stop offset="1" stop-color="var(--navy-deep)"/>
        </linearGradient>
      </defs>
      <polygon points="0,183 274,389 274,480 0,480" fill="url(#navyFade)"/>
      <polygon points="274,192 274,361 173,286.5" fill="var(--navy)"/>
      <polygon points="0,157 0,167 274,372 274,362" fill="var(--berry)"/>
      <line x1="0" y1="173" x2="274" y2="379" stroke="var(--hairline)" stroke-width="1"/>
      <line x1="0" y1="179" x2="274" y2="385" stroke="var(--hairline)" stroke-width="0.8"/>
      <line x1="274" y1="182" x2="167" y2="282" stroke="var(--hairline)" stroke-width="1"/>
      <line x1="274" y1="174" x2="162" y2="278.4" stroke="var(--hairline)" stroke-width="0.8"/>
    </svg>

    <h1 class="brand-name">BildeVOLD</h1>
    <h2 class="holder-name">Henrik Audun Strandvik</h2>
    <p class="holder-role">Dagligleder og Fotograf</p>

    <div class="social-dots">
      <span class="social-dot social-dot--facebook"></span>
      <span class="social-dot social-dot--instagram"></span>
    </div>

    <ul class="contact-list">
      <li>Mobile: +4791264085</li>
      <li>Email: post@bildevold.example</li>
      <li>Web: www.bildevold.example</li>
    </ul>
    <address class="postal-address">Kvernbakken9, 6040 Fjellvika</address>
  </article>
</body>
</html>
```